Spirits Bottle Label-Brand Name Reed & Barrow

Design a spirits bottle label per specifications outlined. Label size Front 3.875x 4.5,Back 2x4, topper 1x5.7. Must have established 2020, 40% Alcohol by volume. 40 proof. Sherry Cask Settled. Bottle # 1 of 1320. Caribbean Rum. Trademark logo must be on the label. Back of label has to have all the information outlined in photo. Topper & Front of the label the designer can you his creativity. Color scheme is negotiable and designers can be creative.

Target Market(s)

Adults aged 21 with an appealing appearance that caters to a young professionals and seasoned adults

Font styles to use
Sans Serif

Colors
886aae
33b8a4
33a6d7

Requirements
Must have
• -Reed & Barrow Trademark Logo which is attached.
-Caribbean Rum
-40% Alcohol By Volume
-80 Proof
-Sherry Cask Settled
-Established 2020

```html
<!DOCTYPE html>
<html lang="en">
<head>
<meta charset="utf-8">
<title>Reed &amp; Barrow — Caribbean Rum Label</title>
<link rel="stylesheet" href="https://fonts.googleapis.com/css2?family=Bebas+Neue&family=Cinzel:wght@700&family=Playfair+Display:wght@700&family=Yellowtail&family=Montserrat:wght@600;800&display=swap">
<style>
  :root {
    --paper: #f8f8ec;
    --teal: #33b5a4;
    --ink: #151515;
    --frame-red: #e0141e;
    --scene-light: #f1f1e6;
    --scene-mid: #dcdcd2;
    --white: #ffffff;
  }
  html, body {
    margin: 0;
    padding: 0;
    width: 1200px;
    height: 1033px;
    overflow: hidden;
    background: var(--paper);
  }
  .label { display: block; width: 1200px; height: 1033px; }
  .brand-title { font-family: "Bebas Neue", sans-serif; fill: var(--ink); }
  .serif-caps { font-family: "Cinzel", serif; font-weight: 700; fill: var(--ink); }
  .proof-number { font-family: "Playfair Display", serif; font-weight: 700; fill: var(--ink); font-variant-numeric: lining-nums; font-feature-settings: "lnum" 1; }
  .script { font-family: "Yellowtail", cursive; font-weight: 400; fill: var(--teal); }
  .band-text { font-family: "Montserrat", sans-serif; font-weight: 600; fill: var(--white); }
  .arc-text { font-family: "Montserrat", sans-serif; font-weight: 800; fill: var(--ink); }
  .mark-name { font-family: "Bebas Neue", sans-serif; fill: var(--paper); }
</style>
</head>
<body>
<svg class="label" viewBox="0 0 1200 1033" xmlns="http://www.w3.org/2000/svg">
  <defs>
    <linearGradient id="sceneTone" x1="0" y1="0" x2="1" y2="1">
      <stop offset="0" stop-color="var(--scene-mid)"/>
      <stop offset="0.5" stop-color="var(--scene-light)"/>
      <stop offset="1" stop-color="var(--scene-mid)"/>
    </linearGradient>
    <path id="autenticArc" d="M462,534 Q602,482 743,534"/>
    <path id="sherryArc" d="M398,790 Q602,990 808,790"/>
  </defs>

  <!-- outer frame -->
  <rect class="outer-frame" x="34" y="27" width="1136" height="974" rx="12" fill="none" stroke="var(--frame-red)" stroke-width="2.5"/>
  <rect class="teal-frame" x="49" y="40" width="1107" height="940" rx="8" fill="var(--teal)"/>
  <rect class="paper-field" x="59" y="50" width="1087" height="790" fill="var(--paper)"/>

  <!-- background scene area -->
  <rect class="scene-art" role="img" aria-label="Faint sketched tropical shoreline with palm trees, sugar cane and a sailing ship" x="59" y="50" width="1087" height="790" fill="url(#sceneTone)" opacity="0.55"/>

  <!-- curved cream tab -->
  <path class="arc-tab" d="M395,838 Q602,1010 810,838 Z" fill="var(--paper)"/>

  <!-- brand mark -->
  <g class="brand-mark">
    <circle cx="602" cy="176" r="119" fill="var(--ink)"/>
    <text class="mark-name" x="602" y="190" font-size="40" text-anchor="middle" letter-spacing="1">REED &amp; BARROW</text>
  </g>

  <!-- brand title -->
  <text class="brand-title" x="248" y="468" font-size="190" textLength="710" lengthAdjust="spacingAndGlyphs">REED &amp; BARROW</text>

  <text class="serif-caps" font-size="32" letter-spacing="4">
    <textPath href="#autenticArc" startOffset="50%" text-anchor="middle">AUTENTIC</textPath>
  </text>

  <g class="divider-dots" fill="var(--ink)">
    <circle cx="538" cy="554" r="4"/><circle cx="567" cy="554" r="6"/>
    <circle cx="602" cy="554" r="10"/><circle cx="637" cy="554" r="6"/><circle cx="666" cy="554" r="4"/>
  </g>

  <text class="script" x="315" y="648" font-size="104" textLength="578" lengthAdjust="spacingAndGlyphs">Caribbean Rum</text>

  <text class="serif-caps" x="292" y="722" font-size="36" textLength="614" lengthAdjust="spacing">SMALL BATCH CRAFTED</text>

  <g class="established">
    <line x1="456" y1="752" x2="527" y2="752" stroke="var(--teal)" stroke-width="3"/>
    <line x1="456" y1="794" x2="527" y2="794" stroke="var(--teal)" stroke-width="3"/>
    <text class="serif-caps" x="491" y="785" font-size="28" text-anchor="middle" letter-spacing="2">EST.</text>
    <line x1="673" y1="750" x2="743" y2="750" stroke="var(--teal)" stroke-width="3"/>
    <line x1="673" y1="792" x2="743" y2="792" stroke="var(--teal)" stroke-width="3"/>
    <text class="serif-caps" x="706" y="785" font-size="28" text-anchor="middle" letter-spacing="2">2020</text>
    <text class="proof-number" x="603" y="803" font-size="76" text-anchor="middle">80</text>
    <text class="serif-caps" x="603" y="838" font-size="22" text-anchor="middle" letter-spacing="3">PROOF</text>
  </g>

  <text class="arc-text" font-size="32" letter-spacing="1">
    <textPath href="#sherryArc" startOffset="50%" text-anchor="middle">SHERRY CASK SETTLED</textPath>
  </text>

  <!-- bottom band details -->
  <text class="band-text" x="176" y="881" font-size="21" letter-spacing="2">750 ML.</text>
  <text class="band-text" x="172" y="924" font-size="21">ALC. BY VOL. 40%</text>

  <text class="band-text" x="966" y="876" font-size="21" text-anchor="middle" letter-spacing="2">BOTTLE NO.</text>
  <rect class="bottle-number-box" x="851" y="895" width="230" height="54" rx="12" fill="var(--white)"/>

  <g class="band-dots" fill="var(--white)">
    <circle cx="537" cy="929" r="4.5"/><circle cx="567" cy="936" r="8"/>
    <circle cx="601" cy="938" r="11"/><circle cx="636" cy="934" r="8"/><circle cx="667" cy="929" r="4.5"/>
  </g>
</svg>
</body>
</html>
```